Byte Wardens Inc. IT Services and Sales

We need a new business card design for our new company. We have a current logo but are open and encourage any redesigns.

Byte Wardens is derived in our history from computer gaming. (NovaSiege References, STORM UNBROKEN!!!). We as a group have been together since high school (2002). Our friendships brought us together and now we are all business partners providing IT Support and Consultation Services ranging from fixing small issues like printers, home networking, pc building to custom application development and managed cloud and it networks for our clients.
We would like our design to communicate that we strive to be the best (we are born gamers and have a highly competitive instinct) and offer solutions to problems that other companies just simply say we can't do it. We are always looking to go above and beyond for our clients, learning our clients business and figuring out ways to help them make more money by optimizing the way they do business, offering solutions so they can grow their business and helping everyone utilize the technology they have or advise them with the technology they need to succeed.

Attached are things we have on our computers and logo's we have used.
One is a desktop background
while the other should be our logo.

Again, we are open to and encourage any logo redesigns in hope things can help with the direction we are looking into.

Please add a place for email as our current cards have no email and it makes us very sad.
Updates

Hi All,

Just wanted to say thank you for all those who submitted a design. We've updated our project to include the fact that we are open and encourage a logo redesign. Also, this project is now committed to payment.

Target Market(s)

We will be handing these out to all our future business prospects. Prospects are usually business owners that can be in any industry. They look to us to be cutting edge or professional.

Industry/Entity Type

High School

Requirements
Must have
• name, title, work, fax, and cell phone, address and email

```html
<!DOCTYPE html>
<html lang="en">
<head>
<meta charset="utf-8">
<title>Byte Wardens Inc. – Business Card</title>
<link rel="stylesheet" href="https://fonts.googleapis.com/css2?family=Open+Sans:wght@300;400;600;700&display=swap">
<style>
  :root {
    --backdrop: #c9c9c9;
    --card: #3a3a3b;
    --text-light: #f2f2f2;
    --text-muted: #c8c8c8;
    --accent-orange: #e8592a;
    --accent-blue: #3fb6ec;
  }
  * { box-sizing: border-box; margin: 0; padding: 0; }
  html, body {
    width: 1200px; height: 1000px; overflow: hidden;
    background: var(--backdrop);
    font-family: "Open Sans", Arial, sans-serif;
  }
  .sheet { position: relative; width: 1200px; height: 1000px; }
  .card {
    position: absolute;
    left: 215px;
    width: 770px; height: 440px;
    background: var(--card);
    border-radius: 26px;
    box-shadow: 0 10px 24px rgba(0,0,0,0.25);
    overflow: hidden;
  }
  .card--front { top: 40px; }
  .card--back { top: 520px; }

  .brand {
    display: flex; align-items: center; gap: 18px;
    color: var(--text-light);
    font-weight: 300;
    white-space: nowrap;
  }
  .brand__dot {
    border-radius: 50%;
    background: var(--accent-blue);
    flex: none;
  }

  /* Front */
  .card--front .brand {
    position: absolute; left: 70px; top: 120px;
    font-size: 84px; letter-spacing: 1px;
  }
  .card--front .brand__dot { width: 64px; height: 64px; }
  .tagline {
    position: absolute; left: 60px; right: 60px; top: 330px;
    color: var(--text-light);
    font-size: 19px; font-weight: 600; letter-spacing: 2px;
    white-space: nowrap;
  }

  /* Back */
  .card--back .brand {
    position: absolute; left: 55px; top: 160px;
    font-size: 44px;
  }
  .card--back .brand__dot { width: 34px; height: 34px; }
  .person { position: absolute; left: 430px; top: 38px; }
  .person__name {
    color: var(--accent-orange);
    font-size: 24px; font-weight: 600; letter-spacing: 0.5px;
  }
  .person__title { color: var(--text-muted); font-size: 18px; }
  .contacts {
    position: absolute; left: 430px; top: 140px;
    list-style: none;
  }
  .contacts li {
    display: flex; align-items: center; gap: 12px;
    color: var(--text-light);
    font-size: 19px; height: 32px;
    white-space: nowrap;
  }
  .contacts svg { width: 18px; height: 18px; flex: none; fill: var(--accent-orange); }
  .address {
    position: absolute; left: 430px; top: 330px;
    color: var(--text-muted);
    font-size: 19px; line-height: 1.35; font-style: normal;
  }
</style>
</head>
<body>
<main class="sheet">
  <section class="card card--front" aria-label="Card front">
    <div class="brand">
      <span class="brand__dot"></span>
      <span class="brand__name">Byte Wardens</span>
    </div>
    <p class="tagline">RETAIL | IT SERVICES | IT CONSULTATION | MARKETING</p>
  </section>

  <section class="card card--back" aria-label="Card back">
    <div class="brand">
      <span class="brand__dot"></span>
      <span class="brand__name">Byte Wardens</span>
    </div>

    <div class="person">
      <h1 class="person__name">MARCUS LINDELL</h1>
      <p class="person__title">Director of Operations</p>
    </div>

    <ul class="contacts">
      <li>
        <svg viewBox="0 0 18 18" aria-hidden="true"><path d="M5 1h8a1 1 0 0 1 1 1v14a1 1 0 0 1-1 1H5a1 1 0 0 1-1-1V2a1 1 0 0 1 1-1zm1 2v9h6V3zm3 10.5a1 1 0 1 0 0 2 1 1 0 0 0 0-2z"/></svg>
        <span>(555) 731 0142</span>
      </li>
      <li>
        <svg viewBox="0 0 18 18" aria-hidden="true"><path d="M4 1.5l3 3-1.6 2.2a11 11 0 0 0 5.9 5.9L13.5 11l3 3-2.2 2.5C8 16 2 10 1.5 3.7z"/></svg>
        <span>(555) 338 0187</span>
      </li>
      <li>
        <svg viewBox="0 0 18 18" aria-hidden="true"><path d="M5 1h7l2 2v4H5zM2 8h14a1 1 0 0 1 1 1v6a1 1 0 0 1-1 1H2a1 1 0 0 1-1-1V9a1 1 0 0 1 1-1zm2 3v1.5h10V11z"/></svg>
        <span>(555) 962 0133</span>
      </li>
      <li>
        <svg viewBox="0 0 18 18" aria-hidden="true"><path d="M1 4h16v10H1zm1.5 1.2V6l6.5 4.3L15.5 6v-.8z"/></svg>
        <span>yourname@bytewardens.com</span>
      </li>
    </ul>

    <address class="address">4470 Cedar Crest Ave.,<br>Suite C, Lakemont, CA. 91999</address>
  </section>
</main>
</body>
</html>
```